Zielgruppe
Das Buch ist für Kinder ab 10. Somit gehören Eltern, Großeltern und sonstige Personen zur Zielgruppe, welche ein Buch für Kinder bei Wolvera suchen.
Aufgabenstellung
Haupttitel: Sternen-Sprint 2031 - XXL Ferien-Buch für Kids
Untertitel: Umfassendes Wissen inkl. Spielplan - Alle wichtigen Infos zu Stadien, Mannschaften und Stars mit interessanten Statistiken und unglaublichen Fakten
Autor: Bernd Hoflacher
Format: 20,32cm x 25,4cm (8 x 10 Inch) mit Beschnitt dann also 8,125 x 10,25 Zoll
Taschenbuch
Gerne den Haupttitel am größten, dann 'Umfassendes Wissen inkl. Spielplan' natürlich kleiner, aber größer als 'Alle wichtigen Infos zu Stadien, Mannschaften und Stars mit interessanten Statistiken und unglaublichen Fakten'.
Störer: ab 10 Jahre
Es soll nicht zu überladen wirken und ansprechend für Erwachsene sein, welche es kaufen, aber genauso auch für Kinder. Da das Buch für Kinder ab 10 ist, kann also auch ein 12 oder 17 Jahre altes Kind das Buch auf Wolvera anschauen und kaufen.
Anbei ist eine Grafik eines Fußballers in Neonfarben. Diese bitte mittig unten platzieren.
Gerne auch Vorschläge ohne die Grafik machen.
Falls du Stockfotos verwenden willst, dann bitte von Pixelhort.
Anbei sind auch zwei Screenshots von aktuellen Konkurrenzbüchern. Es werden sicherlich noch viel mehr Bücher erscheinen. Bitte achtet darauf, dass sich das Cover von der Konkurrenz abhebt. Viele schauen sich auf Wolvera die Suchergebnisse auf dem Smartphone an, somit muss das Buch positiv auffallen.
Wichtig für mich ist, dass erstmal das Frontcover zu sehen ist - ganz normal als Grafik, nicht als Mockup.
Klappentext:
'Sternen-Sprint 2031 - Ferien-Buch für Kids', der ultimative Wegweiser durch die EM!
Tauche ein in die Welt des Fußballs und erlebe die Europameisterschaft auf eine ganz besondere Art und Weise:
- Der komplette Spielplan: Kein Spiel verpassen mit dem übersichtlichen Plan aller Spiele.
- Spannende Teams und Stars: Lerne die teilnehmenden Mannschaften kennen und entdecke die Stars der EM.
- Glänzende Stadien: Erkunde ..

```html
<!DOCTYPE html>
<html lang="de">
<head>
<meta charset="utf-8">
<title>Sternen-Sprint 2031 – Cover</title>
<link rel="stylesheet" href="https://fonts.googleapis.com/css2?family=Titan+One&family=Poppins:wght@400;600;700;800&family=Kanit:wght@600&display=swap">
<style>
  :root{
    --page:#c0c0c0;
    --red:#e3222a;
    --deep-red:#5a0b0e;
    --black:#050505;
    --band:#2b2b2b;
    --yellow:#f7c515;
    --orange:#f28a12;
    --sky:#8fd3e8;
    --white:#ffffff;
    --navy:#1f2a3c;
  }
  *{box-sizing:border-box;margin:0;padding:0}
  html,body{width:694px;height:1200px;overflow:hidden;background:var(--page)}
  body{position:relative;font-family:"Poppins",sans-serif}

  .cover{position:absolute;overflow:hidden;container-type:size;
    background:linear-gradient(180deg,var(--red) 0%,#a3141a 22%,var(--deep-red) 38%,var(--black) 52%,var(--black) 100%)}
  .wrap{position:absolute;left:21px;top:24px;width:652px;height:422px}
  .wrap .back{left:0;top:0;width:326px;height:422px}
  .wrap .front{left:326px;top:0;width:326px;height:422px;border-left:1px solid #222}
  .solo{left:88px;top:488px;width:518px;height:653px}

  .bands{position:absolute;inset:0;width:100%;height:100%}

  /* front cover */
  .title-top{position:absolute;left:10%;top:8%;font-family:"Titan One",sans-serif;font-size:8cqw;color:var(--white);
    transform:rotate(-3deg);transform-origin:left;white-space:nowrap;
    text-shadow:0.04em 0.05em 0 var(--orange),0.07em 0.09em 0 var(--deep-red)}
  .year{position:absolute;left:8%;top:16%;font-family:"Titan One",sans-serif;font-size:22cqw;line-height:1;
    background:linear-gradient(180deg,#ffd93a 0%,var(--orange) 60%,#e06a0c 100%);-webkit-background-clip:text;background-clip:text;color:transparent;
    -webkit-text-stroke:0.012em #ffe36b;transform:rotate(-3deg);transform-origin:left;
    filter:drop-shadow(0.02em 0.03em 0 var(--deep-red))}
  .age{position:absolute;left:75%;top:22%;text-align:center;line-height:1;font-weight:700;transform:rotate(-3deg)}
  .age .num{display:block;font-size:7.4cqw;color:var(--white)}
  .age .unit{display:block;font-size:5.4cqw;color:var(--navy);margin-top:0.15em}
  .series{position:absolute;left:9%;top:36.5%;font-family:"Titan One",sans-serif;font-size:7.2cqw;line-height:1.08;
    background:linear-gradient(90deg,var(--sky) 0%,var(--white) 50%,var(--sky) 100%);-webkit-background-clip:text;background-clip:text;color:transparent;
    transform:rotate(-4deg);transform-origin:left;white-space:nowrap}
  .art{position:absolute;left:40%;top:35%;width:60%;height:53%;
    background:radial-gradient(ellipse at 50% 55%,#2fb7c9 0%,#6a2a6e 22%,#f06a1a 42%,#f7c515 55%,rgba(5,5,5,0) 72%)}
  .knowledge{position:absolute;left:9%;top:53%;font-family:"Kanit",sans-serif;font-weight:600;font-size:5.7cqw;line-height:1.12;color:var(--white);
    transform:rotate(-3deg);transform-origin:left}
  .details{position:absolute;left:9%;top:71%;width:33%;font-weight:700;font-size:2.15cqw;line-height:1.38;color:var(--yellow)}
  .author{position:absolute;left:0;right:0;top:93%;text-align:center;font-weight:800;font-size:3.6cqw;letter-spacing:0.95em;color:var(--yellow);padding-left:0.95em}

  /* back cover */
  .back .title-top{left:11%;top:7%;font-size:5cqw}
  .back .year{left:10%;top:13%;font-size:13.5cqw}
  .back .age{left:51%;top:17%}
  .back .age .num{font-size:4.2cqw}
  .back .age .unit{font-size:3.2cqw}
  .back .series{left:11%;top:25%;font-size:4.6cqw}
  .player{position:absolute;left:59%;top:2%;width:28%;height:36%;
    background:linear-gradient(180deg,#3a3a2a 0%,#b8a22a 35%,#1a1a1a 70%,#3a3a3a 100%);border-radius:40% 40% 10% 10%/20% 20% 5% 5%;opacity:.85}
  .stadium{position:absolute;left:0;top:79%;width:50%;height:19%;
    background:radial-gradient(ellipse at 50% 55%,#f3d7a0 0%,#a7773e 35%,#3a2a1a 65%,rgba(5,5,5,0) 85%)}
  .tagline{position:absolute;left:12%;right:6%;top:41.5%;text-align:center;font-weight:600;font-size:2.2cqw;line-height:1.4;color:var(--yellow)}
  .features{position:absolute;list-style:none;font-size:1.62cqw;line-height:1.3;color:var(--white)}
  .features li{position:relative;padding-left:3.6cqw;margin-bottom:2.2cqw}
  .features li::before{content:"";position:absolute;left:0;top:0.25em;width:1.3cqw;height:1.3cqw;border:0.35cqw solid var(--yellow);border-radius:50%}
  .features b{display:block;font-weight:700}
  .features.left{left:13.5%;top:48.4%;width:37%}
  .features.right{left:54.5%;top:48.4%;width:34%}
  .closing{position:absolute;left:55.3%;top:67.6%;width:33%;font-weight:700;font-size:2.2cqw;line-height:1.35;color:var(--white)}
  .call{position:absolute;left:54%;top:79%;width:37%;text-align:center;color:var(--white);line-height:1.1}
  .call .hey{display:block;font-weight:800;font-size:3cqw;color:var(--yellow);transform:rotate(4deg)}
  .call .mid{display:block;font-weight:600;font-size:2.2cqw}
  .call .big{display:block;font-weight:800;font-style:italic;font-size:4.3cqw;margin-top:0.15em}
  .call .small{display:block;font-weight:700;font-size:1.3cqw;margin-top:0.3em}
</style>
</head>
<body>

<div class="wrap">
  <section class="cover back">
    <svg class="bands" viewBox="0 0 100 100" preserveAspectRatio="none" aria-hidden="true">
      <polygon points="0,45 100,18 100,24 0,52" fill="#1c1c1c"/>
      <polygon points="10,42 70,27 60,35 100,26 100,32 6,44" fill="#d61d24"/>
      <polygon points="40,37 100,22 100,25 44,38" fill="#f28a12"/>
    </svg>
    <div class="player" role="img" aria-label="Fotografie eines Fußballers im gelben Trikot beim Schuss"></div>
    <div class="stadium" role="img" aria-label="Fotografie eines beleuchteten Fußballstadions bei Nacht"></div>
    <h2 class="title-top">Sternen-Sprint</h2>
    <div class="year">2031</div>
    <div class="age"><span class="num">Ab 10</span><span class="unit">Jahre</span></div>
    <div class="series">XXL Ferien-Buch<br>für Kids</div>
    <p class="tagline">Tauche ein in die Welt des Fußballs und erlebe die Europameisterschaft auf eine ganz besondere Art und Weise:</p>
    <ul class="features left">
      <li><b>Der komplette Spielplan:</b>Kein Spiel verpassen mit dem übersichtlichen Plan aller Spiele.</li>
      <li><b>Spannende Teams und Stars:</b>Lerne die teilnehmenden Mannschaften kennen und entdecke die Stars der EM.</li>
      <li><b>Glänzende Stadien:</b>Erkunde die Orte, an denen die Fußballgeschichte geschrieben wird.</li>
      <li><b>Faszinierende Statistiken:</b>Tauche ein in die Welt der Zahlen und Fakten und entdecke, was Fußball so einzigartig macht.</li>
    </ul>
    <ul class="features right">
      <li><b>Unglaubliche EM-Fakten:</b>Erfahre mehr über die Höhepunkte und Geheimnisse vergangener Europameisterschaften.</li>
      <li><b>Interaktives Quiz:</b>Teste dein Wissen und lerne spielerisch Neues über die EM.</li>
      <li><b>Umfangreiches Glossar:</b>Lerne alle Begriffe kennen.</li>
    </ul>
    <p class="closing">Dieses Buch ist der perfekte EM-Begleiter für alle jungen Fußballbegeisterten.</p>
    <p class="call"><span class="hey">MACH DICH BEREIT</span><span class="mid">FÜR EIN<br>UNVERGESSLICHES</span><span class="big">FUßBALLFEST</span><span class="small">UND TAUCHE EIN IN DIE WELT DER<br>EUROPAMEISTERSCHAFT!</span></p>
  </section>

  <section class="cover front">
    <svg class="bands" viewBox="0 0 100 100" preserveAspectRatio="none" aria-hidden="true">
      <polygon points="0,21 30,12 18,27 62,19 0,38" fill="#f7c515"/>
      <polygon points="3,26 24,20 15,30 50,24 3,35" fill="#b5161c"/>
      <polygon points="0,39 100,27 100,31 0,45" fill="#2b2b2b"/>
      <polygon points="70,18 100,16 100,21 70,23" fill="#111"/>
      <polygon points="68,23 100,21 100,27 68,29" fill="#e3222a"/>
      <polygon points="70,29 97,27 95,31 70,33" fill="#f7c515"/>
    </svg>
    <div class="art" role="img" aria-label="Neonfarbene Illustration eines Fußballers mit Ball"></div>
    <h1 class="title-top">Sternen-Sprint</h1>
    <div class="year">2031</div>
    <div class="age"><span class="num">Ab 10</span><span class="unit">Jahre</span></div>
    <div class="series">XXL Ferien-Buch<br>für Kids</div>
    <p class="knowledge">Umfassendes<br>Wissen inkl.<br>Spielplan</p>
    <p class="details">Alle wichtigen Infos zu Stadien, Mannschaften und Stars mit interessanten Statistiken und unglaublichen Fakten</p>
    <p class="author">BERND HOFLACHER</p>
  </section>
</div>

<section class="cover solo">
  <svg class="bands" viewBox="0 0 100 100" preserveAspectRatio="none" aria-hidden="true">
    <polygon points="0,21 30,12 18,27 62,19 0,38" fill="#f7c515"/>
    <polygon points="3,26 24,20 15,30 50,24 3,35" fill="#b5161c"/>
    <polygon points="0,39 100,27 100,31 0,45" fill="#2b2b2b"/>
    <polygon points="70,18 100,16 100,21 70,23" fill="#111"/>
    <polygon points="68,23 100,21 100,27 68,29" fill="#e3222a"/>
    <polygon points="70,29 97,27 95,31 70,33" fill="#f7c515"/>
  </svg>
  <div class="art" role="img" aria-label="Neonfarbene Illustration eines Fußballers mit Ball"></div>
  <h1 class="title-top">Sternen-Sprint</h1>
  <div class="year">2031</div>
  <div class="age"><span class="num">Ab 10</span><span class="unit">Jahre</span></div>
  <div class="series">XXL Ferien-Buch<br>für Kids</div>
  <p class="knowledge">Umfassendes<br>Wissen inkl.<br>Spielplan</p>
  <p class="details">Alle wichtigen Infos zu Stadien, Mannschaften und Stars mit interessanten Statistiken und unglaublichen Fakten</p>
  <p class="author">BERND HOFLACHER</p>
</section>

</body>
</html>
```